Torvane Halbridge

Looking for modern business cards.
Clean contemporary design.
Similar to this.
https://www.plumvexa-search.example/imgres?imgurl=https%3A%2F%2Fimg.quorlint-cdn.example%2Fsleek_dark_metal_card_design_540.jpg&imgrefurl=https%3A%2F%2Fwww.quorlint-prints.example%2Fsleek_dark_metal_card_design-918273645501928374&q=modern%20business%20cards

But I'd like the blue to look metallic.

Business

```html
<!DOCTYPE html>
<html lang="en">
<head>
<meta charset="utf-8">
<title>Torvane Halbridge — Business Card</title>
<link rel="stylesheet" href="https://fonts.googleapis.com/css2?family=Roboto:ital,wght@0,400;0,500;1,700&display=swap">
<style>
  :root {
    --backdrop: #e6e8ea;
    --paper: #f4f5f5;
    --navy: #22536a;
    --navy-deep: #1b4457;
    --navy-light: #2d6a86;
    --sky: #2a9abf;
    --accent: #e8432a;
    --white: #ffffff;
    --icon: #b9d3df;
  }
  * { margin: 0; padding: 0; box-sizing: border-box; }
  html, body {
    width: 1200px; height: 960px; overflow: hidden;
    background: var(--backdrop);
    font-family: "Roboto", Arial, sans-serif;
  }
  .canvas { position: relative; width: 1200px; height: 960px; }

  .card {
    position: absolute; width: 600px; height: 343px; overflow: hidden;
    box-shadow: 0 3px 8px rgba(0,0,0,.25);
  }
  .card-front { left: 315px; top: 113px; background: var(--paper); }
  .card-back {
    left: 312px; top: 472px;
    background: linear-gradient(135deg, var(--navy-light) 0%, var(--navy) 45%, var(--navy-deep) 100%);
  }

  .front-band { position: absolute; left: 0; top: 0; width: 600px; height: 343px; }

  .brand {
    position: absolute; left: 140px; top: 98px;
    display: flex; align-items: center; gap: 10px;
  }
  .brand-name {
    font-size: 32px; font-weight: 400; color: var(--navy);
    letter-spacing: -0.5px; white-space: nowrap; line-height: 40px;
  }
  .brand-dot {
    width: 10px; height: 10px; border-radius: 50%; background: var(--accent);
  }
  .tagline {
    position: absolute; left: 215px; top: 139px; width: 205px;
    font-size: 7px; font-weight: 700; font-style: italic;
    color: var(--sky); letter-spacing: .4px; white-space: nowrap;
  }

  .identity {
    position: absolute; right: 320px; top: 234px; text-align: right; color: var(--white);
  }
  .person-name { font-size: 19px; font-weight: 500; color: var(--sky); line-height: 24px; }
  .person-role { font-size: 14px; font-weight: 500; line-height: 20px; }
  .address { font-size: 14px; line-height: 19px; }

  .divider {
    position: absolute; left: 299px; top: 231px; width: 1px; height: 88px;
    background: rgba(255,255,255,.55);
  }

  .contacts { position: absolute; left: 320px; top: 238px; list-style: none; color: var(--white); }
  .contacts li { display: flex; align-items: center; height: 19.3px; font-size: 14px; white-space: nowrap; }
  .contacts svg { width: 14px; height: 14px; margin-right: 8px; fill: var(--icon); }

  .back-mark {
    position: absolute; left: 0; top: 150px; width: 600px;
    display: flex; justify-content: center; align-items: center; gap: 14px;
  }
  .back-name { font-size: 40px; font-weight: 400; color: var(--white); letter-spacing: -0.5px; }
  .back-dot { width: 18px; height: 18px; border-radius: 50%; background: var(--accent); }
  .website {
    position: absolute; left: 0; top: 288px; width: 600px; text-align: center;
    font-size: 14px; letter-spacing: 2.6px; color: var(--white);
  }
</style>
</head>
<body>
<main class="canvas">

  <section class="card card-front">
    <svg class="front-band" viewBox="0 0 600 343" aria-hidden="true">
      <defs>
        <linearGradient id="metal" x1="0" y1="0" x2="1" y2="1">
          <stop offset="0" stop-color="#2d6a86"/>
          <stop offset=".45" stop-color="#22536a"/>
          <stop offset="1" stop-color="#1b4457"/>
        </linearGradient>
      </defs>
      <path d="M0 182 Q300 225 600 176 L600 343 L0 343 Z" fill="url(#metal)"/>
      <path d="M45 178 Q320 222 600 170 L600 180 Q320 218 45 178 Z" fill="var(--sky)"/>
    </svg>

    <div class="brand">
      <span class="brand-name">Torvane Halbridge</span>
      <span class="brand-dot"></span>
    </div>
    <p class="tagline">"Steady leadership for every stage of growth"</p>

    <div class="identity">
      <p class="person-name">MAREK OSTRAND</p>
      <p class="person-role">CEO/FOUNDER</p>
      <p class="address">4821 Alderwick Road</p>
      <p class="address">Brenmoor, Calvane 58213</p>
    </div>

    <div class="divider"></div>

    <ul class="contacts">
      <li><svg viewBox="0 0 24 24"><path d="M6.6 10.8a15 15 0 0 0 6.6 6.6l2.2-2.2c.3-.3.7-.4 1-.2 1.1.4 2.3.6 3.6.6.6 0 1 .4 1 1V20c0 .6-.4 1-1 1A17 17 0 0 1 3 4c0-.6.4-1 1-1h3.5c.6 0 1 .4 1 1 0 1.3.2 2.5.6 3.6.1.3 0 .7-.2 1z"/></svg>604 218 7395</li>
      <li><svg viewBox="0 0 24 24"><path d="M7 1h10a2 2 0 0 1 2 2v18a2 2 0 0 1-2 2H7a2 2 0 0 1-2-2V3a2 2 0 0 1 2-2zm0 3v14h10V4zm5 15.5a1 1 0 1 0 0 2 1 1 0 0 0 0-2z"/></svg>715 382 9046</li>
      <li><svg viewBox="0 0 24 24"><path d="M6 2h12v5H6zM3 8h18a2 2 0 0 1 2 2v7h-4v5H5v-5H1v-7a2 2 0 0 1 2-2zm4 7v5h10v-5z"/></svg>539 760 2184</li>
      <li><svg viewBox="0 0 24 24"><path d="M2 5h20v14H2zm2 2v.5l8 5 8-5V7l-8 5z"/></svg>marek@torvanehalbridge.example</li>
    </ul>
  </section>

  <section class="card card-back">
    <div class="back-mark">
      <p class="back-name">Torvane Halbridge</p>
      <span class="back-dot"></span>
    </div>
    <p class="website">www.torvanehalbridge.example</p>
  </section>

</main>
</body>
</html>
```